real esate business card with company logo and name

we need a business card design for a real esate company

The company name is Walsh & Brand Pty Ltd, and we have our logo designed and will upload. We want classic or moden feel. Black or white background. looks more textured. Should include folowinginformations
Owen Walsh and Lucy Brand
Sales Agents & Onsite Manager
p: 07 5948 2063
F: 07 5948 2174
M:0431 857 219
3/42 Marlow Crescent, FERNLEA QLD 4213

We want this business card looks professonal. Thank you in advance.

Industry/Entity Type

Real Estate Agent

Contact Information for Business Card

Owen Walsh and Lucy Brand
Onsite Manager & Sales Agents
p: 07 5948 2063
M:0431 857 219

Font styles to use
Serif

Colors
000000
fbfbfb
333333
959595

Requirements
Must have
• company logo and name, black or white back ground

```html
<!DOCTYPE html>
<html lang="en">
<head>
<meta charset="utf-8">
<title>Walsh &amp; Brand Pty Ltd — Business Card</title>
<link rel="stylesheet" href="https://fonts.googleapis.com/css2?family=Gabriela&family=Tinos:wght@400&display=swap">
<style>
  :root {
    --page: #fbfbfb;
    --card-frost-light: #e6e3de;
    --card-frost-dark: #d3cfc9;
    --panel-top: #333333;
    --panel-bottom: #161616;
    --ink-grey: #959595;
    --name-light: #f1eee8;
    --detail-tan: #c8b79c;
  }
  * { box-sizing: border-box; margin: 0; padding: 0; }
  html, body {
    width: 1200px;
    height: 970px;
    overflow: hidden;
    background: var(--page);
  }
  .business-card {
    position: absolute;
    left: 100px;
    top: 185px;
    width: 1000px;
    height: 600px;
    background: linear-gradient(135deg, var(--card-frost-light), var(--card-frost-dark));
    box-shadow: 0 10px 30px rgba(0, 0, 0, 0.18);
    overflow: hidden;
  }
  .contact-panel {
    position: absolute;
    inset: 0;
    width: 1000px;
    height: 600px;
  }
  .brand-block {
    position: absolute;
    left: 23px;
    top: 300px;
    width: 300px;
    display: flex;
    flex-direction: column;
    align-items: center;
    gap: 22px;
  }
  .brand-square {
    width: 150px;
    height: 150px;
    background: var(--ink-grey);
  }
  .brand-name {
    font-family: "Tinos", serif;
    font-size: 21px;
    letter-spacing: 1.5px;
    text-transform: uppercase;
    color: var(--ink-grey);
    white-space: nowrap;
  }
  .brand-block { top: 170px; }
  .card-details {
    position: absolute;
    left: 383px;
    width: 600px;
    top: 0;
    text-align: center;
  }
  .agent-names {
    position: absolute;
    top: 118px;
    width: 100%;
    font-family: "Gabriela", serif;
    font-size: 42px;
    color: var(--name-light);
    white-space: nowrap;
  }
  .agent-role {
    position: absolute;
    top: 193px;
    width: 100%;
    font-family: "Tinos", serif;
    font-size: 23px;
    color: var(--detail-tan);
  }
  .contact-lines {
    position: absolute;
    top: 322px;
    width: 100%;
    font-family: "Tinos", serif;
    font-size: 26px;
    line-height: 38px;
    color: var(--detail-tan);
    list-style: none;
  }
</style>
</head>
<body>
  <div class="business-card">
    <svg class="contact-panel" viewBox="0 0 1000 600" aria-hidden="true">
      <defs>
        <linearGradient id="panelShade" x1="0" y1="0" x2="0" y2="1">
          <stop offset="0" stop-color="var(--panel-top)"/>
          <stop offset="1" stop-color="var(--panel-bottom)"/>
        </linearGradient>
      </defs>
      <path d="M528,0 L1000,0 L1000,600 L640,600 C430,560 300,420 313,271 C320,150 420,40 528,0 Z" fill="url(#panelShade)"/>
    </svg>

    <div class="brand-block">
      <div class="brand-square"></div>
      <div class="brand-name">Walsh &amp; Brand Pty Ltd.</div>
    </div>

    <div class="card-details">
      <h1 class="agent-names">Owen Walsh and Lucy Brand</h1>
      <p class="agent-role">Onsite Manager &amp; Sales Agents</p>
      <ul class="contact-lines">
        <li>07 5948 2063</li>
        <li>0431 857 219</li>
        <li>3/42 Marlow Crescent, FERNLEA</li>
        <li>QLD 4213</li>
      </ul>
    </div>
  </div>
</body>
</html>
```